New tech executive consulting company needs professionally branded document templates

We are a new business selling fractional board advisory and go-to-market consulting services into the Technology space. Tessaly Brink are experts in providing high-quality executive-level leaders on a part-time basis to tech companies in need of their expertise. We work closely with clients to understand their business needs, challenges, and goals, and provides customised solutions to help them succeed. Due to our audience we need the design to have a high quality, executive look and feel.

Our first website is live and can be found at tessalybrink.example. We also already have a logo which I've uploaded. Our brand is clean and uses orange to give it colour and an identity that stands out.

We need some document master templates created so we can create our own presentations (Google Slides & Powerpoint), PDF documents, and Word templates, and ideally also a LinkedIn banner.

```html
<!DOCTYPE html>
<html lang="en">
<head>
<meta charset="utf-8">
<title>Tessaly Brink — Presentation Template</title>
<link href="https://fonts.googleapis.com/css2?family=Open+Sans:wght@400;600;700;800&display=swap" rel="stylesheet">
<style>
:root{
  --navy:#2c3440;
  --orange:#ef8147;
  --ink:#3a3a3a;
  --grey:#9a9ea4;
  --light:#f2f2f2;
  --bg:#e4e6ea;
  --white:#ffffff;
}
*{margin:0;padding:0;box-sizing:border-box}
html,body{width:1200px;height:3413px;overflow:hidden}
body{background:var(--bg);font-family:"Open Sans",Arial,sans-serif;color:var(--ink);position:relative}
.hero-mark{position:absolute;right:48px;top:58px;font-weight:700;font-size:30px;line-height:1.05;letter-spacing:3px;color:var(--navy);text-align:center}
.hero-slide{position:absolute;left:170px;top:330px;transform:scale(1.527);transform-origin:0 0;box-shadow:0 6px 24px rgba(0,0,0,.18)}
.slide{position:absolute;width:563px;height:315px;background:var(--white);overflow:hidden}
.slide>svg.full{position:absolute;left:0;top:0}
.col-l{left:28px}.col-r{left:609px}
.r1{top:719px}.r2{top:1054px}.r3{top:1389px}.r4{top:1725px}
.r5{top:2060px}.r6{top:2395px}.r7{top:2730px}.r8{top:3065px}
.abs{position:absolute}
.mark{position:absolute;right:22px;top:16px;font-weight:700;font-size:8px;line-height:1.05;letter-spacing:.6px;color:var(--navy);text-align:center}
.mark-lg{font-weight:700;font-size:15px;line-height:1.05;letter-spacing:1.2px;text-align:center;position:absolute}
.on-dark{color:var(--white)}
.slash{position:absolute;left:20px;top:20px}
.s-title{position:absolute;left:50px;top:20px;font-size:18px;color:var(--navy);font-weight:400;white-space:nowrap}
.s-title b{font-weight:600}
.foot{position:absolute;right:20px;bottom:14px;font-size:5px;color:var(--navy);display:flex;align-items:center;gap:8px}
.foot b{font-weight:700}
.pg{width:9px;height:9px;background:var(--orange);color:var(--white);font-size:4.5px;display:flex;align-items:center;justify-content:center}
.p{font-size:6.3px;line-height:1.3;color:var(--ink)}
.sub{font-size:10px;color:var(--orange);font-weight:400}
.sub b{font-weight:600}
.bul{list-style:none}
.bul li{position:relative;padding-left:10px;margin-bottom:6px;font-size:6.3px;line-height:1.3}
.bul li::before{content:"";position:absolute;left:0;top:2px;width:3.5px;height:3.5px;border-radius:50%;background:var(--orange)}
.cover-title{position:absolute;left:46px;top:122px;font-weight:700;font-size:21px;line-height:1.15;letter-spacing:.3px}
.cover-lead{position:absolute;left:46px;top:180px;font-size:6.4px;line-height:1.3;width:240px}
.cover-date{position:absolute;left:46px;top:218px;font-size:5.5px}
.cover-copy{position:absolute;left:46px;top:264px;font-size:4.6px}
.agenda-row{position:absolute;left:265px;display:flex;align-items:center;gap:8px}
.agenda-row .num{font-size:16px;color:var(--orange);width:24px}
.agenda-row .bar{width:1px;height:22px;background:var(--grey)}
.agenda-row .t{font-size:7px;color:var(--navy)}
.agenda-row .t small{display:block;font-size:5.2px;color:var(--ink);margin-top:2px}
.ttl{font-size:7px;color:var(--navy)}
.ttl b{font-weight:600}
.icon-sq{position:absolute;width:36px;height:36px;background:var(--orange);border-radius:3px;display:flex;align-items:center;justify-content:center}
.circ{position:absolute;border-radius:50%;display:flex;align-items:center;justify-content:center}
.ph-cap{font-size:6px;line-height:1.3;text-align:center}
.otitle{font-size:9px;color:var(--orange);line-height:1.15}
.otitle b{font-weight:600}
table.data{position:absolute;left:30px;top:84px;width:503px;border-collapse:collapse;font-size:5.4px}
table.data th{height:26px;color:var(--white);font-weight:700;text-align:center;padding:0 4px}
table.data th:first-child{background:var(--navy);text-align:left;padding-left:5px}
table.data th.o{background:var(--orange)}
table.data th.g{background:var(--grey)}
table.data td{height:22.5px;text-align:center;border-bottom:1px solid #ddd}
table.data td:first-child{text-align:left;padding-left:5px;font-weight:700;color:var(--navy)}
table.data tr:nth-child(even) td{background:var(--light)}
.contact-h{position:absolute;left:46px;top:172px;font-weight:700;font-size:9px}
.contact-row{position:absolute;left:46px;display:flex;align-items:center;gap:6px;font-size:5.8px}
</style>
</head>
<body>

<div class="hero-mark">TESSALY<br>BRINK</div>

<!-- Hero: cover slide at large size -->
<div class="slide hero-slide" style="left:170px;top:330px">
  <svg class="full" width="563" height="315" viewBox="0 0 563 315">
    <rect width="563" height="315" fill="#2c3440"/>
    <polygon points="505,0 563,0 563,315 272,315" fill="#4a5664" role="img" aria-label="Photo of business partners shaking hands over a tablet showing a stock chart"/>
    <polygon points="485,0 505,0 272,315 252,315" fill="#ef8147"/>
  </svg>
  <div class="mark-lg on-dark" style="left:46px;top:38px">TESSALY<br>BRINK</div>
  <div class="cover-title on-dark">PRESENTATION<br>TITLE GOES HERE!</div>
  <div class="cover-lead on-dark">Lorem ipsum dolor sit amet, consectetur adipiscing elit. Vivamus eu dui ex. Curabitur dapibus dignissim dui, in molestie.</div>
  <div class="cover-date on-dark">Monday, July 17, 2023</div>
  <div class="cover-copy on-dark">Copyright © 2023 <b>Tessaly Brink</b>. All Rights Reserved.</div>
</div>

<!-- Row 1: cover dark -->
<div class="slide col-l r1">
  <svg class="full" width="563" height="315" viewBox="0 0 563 315">
    <rect width="563" height="315" fill="#2c3440"/>
    <polygon points="505,0 563,0 563,315 272,315" fill="#4a5664" role="img" aria-label="Photo of business partners shaking hands over a tablet showing a stock chart"/>
    <polygon points="485,0 505,0 272,315 252,315" fill="#ef8147"/>
  </svg>
  <div class="mark-lg on-dark" style="left:46px;top:38px">TESSALY<br>BRINK</div>
  <div class="cover-title on-dark">PRESENTATION<br>TITLE GOES HERE!</div>
  <div class="cover-lead on-dark">Lorem ipsum dolor sit amet, consectetur adipiscing elit. Vivamus eu dui ex. Curabitur dapibus dignissim dui, in molestie.</div>
  <div class="cover-date on-dark">Monday, July 17, 2023</div>
  <div class="cover-copy on-dark">Copyright © 2023 <b>Tessaly Brink</b>. All Rights Reserved.</div>
</div>

<!-- Row 1: cover light -->
<div class="slide col-r r1">
  <svg class="full" width="563" height="315" viewBox="0 0 563 315">
    <polygon points="505,0 563,0 563,315 272,315" fill="#4a5664" role="img" aria-label="Photo of business partners shaking hands over a tablet showing a stock chart"/>
    <polygon points="485,0 505,0 272,315 252,315" fill="#ef8147"/>
  </svg>
  <div class="mark-lg" style="left:46px;top:38px;color:var(--navy)">TESSALY<br>BRINK</div>
  <div class="cover-title" style="color:var(--orange)">PRESENTATION<br>TITLE GOES HERE!</div>
  <div class="cover-lead" style="color:var(--navy)">Lorem ipsum dolor sit amet, consectetur adipiscing elit. Vivamus eu dui ex. Curabitur dapibus dignissim dui, in molestie.</div>
  <div class="cover-date" style="color:var(--navy)">Monday, July 17, 2023</div>
  <div class="cover-copy" style="color:var(--navy)">Copyright © 2023 <b>Tessaly Brink</b>. All Rights Reserved.</div>
</div>

<!-- Row 2: agenda -->
<div class="slide col-l r2">
  <svg class="full" width="563" height="315" viewBox="0 0 563 315">
    <polygon points="0,0 245,0 0,315" fill="#5f6d7c" role="img" aria-label="Photo of two people shaking hands"/>
    <polygon points="245,0 272,0 27,315 0,315" fill="#ef8147"/>
  </svg>
  <div class="mark">TESSALY<br>BRINK</div>
  <svg class="abs" style="left:262px;top:76px" width="20" height="26"><line x1="16" y1="2" x2="4" y2="24" stroke="#ef8147" stroke-width="2.2"/></svg>
  <div class="s-title" style="left:292px;top:78px"><b>Agenda</b> Slide</div>
  <div class="agenda-row" style="top:124px"><span class="num">01</span><span class="bar"></span><span class="t"><b>Title</b> Goes Here<small>Lorem Ipsum Dolor Sit Amet, Consectetur Adipiscing Elit.</small></span></div>
  <div class="agenda-row" style="top:160px"><span class="num">02</span><span class="bar"></span><span class="t"><b>Title</b> Goes Here<small>Lorem Ipsum Dolor Sit Amet, Consectetur Adipiscing Elit.</small></span></div>
  <div class="agenda-row" style="top:196px"><span class="num">03</span><span class="bar"></span><span class="t"><b>Title</b> Goes Here<small>Lorem Ipsum Dolor Sit Amet, Consectetur Adipiscing Elit.</small></span></div>
  <div class="agenda-row" style="top:232px"><span class="num">04</span><span class="bar"></span><span class="t"><b>Title</b> Goes Here<small>Lorem Ipsum Dolor Sit Amet, Consectetur Adipiscing Elit.</small></span></div>
  <div class="foot"><span>Copyright © 2023 <b>Tessaly Brink</b>. All Rights Reserved.</span><span class="pg">3</span></div>
</div>

<!-- Row 2: about us -->
<div class="slide col-r r2">
  <svg class="slash" width="20" height="26"><line x1="16" y1="2" x2="4" y2="24" stroke="#ef8147" stroke-width="2.2"/></svg>
  <div class="s-title" style="font-weight:600">ABOUT US</div>
  <div class="mark">TESSALY<br>BRINK</div>
  <div class="abs" role="img" aria-label="Photo of a team reviewing printed charts and a tablet on a desk" style="left:0;top:80px;width:563px;height:192px;background:linear-gradient(90deg,#8a8f95,#c9ccd0)"></div>
  <div class="abs" style="left:60px;top:80px;width:190px;height:192px;background:rgba(239,129,71,.93)"></div>
  <div class="circ" style="left:137px;top:96px;width:36px;height:36px;border:2px solid #fff">
    <svg width="16" height="14" viewBox="0 0 16 14"><rect x="1" y="3" width="14" height="10" rx="1" fill="#fff"/><rect x="5" y="0.5" width="6" height="3" fill="none" stroke="#fff" stroke-width="1.2"/></svg>
  </div>
  <div class="abs p" style="left:75px;top:143px;width:160px;color:#fff;text-align:center">Lorem Ipsum Dolor Sit Amet, Consectetur Adipiscing Elit. Vivamus Eu Dui Ex. Curabitur Dapibus Dignissim Dui, In Molestie Metus Feugiat Sed. Praesent Aliquet Lorem Ex, Eu Dapibus Odio Varius At. Duis Eget Tellus Porta, Consequat Lacus Vitae, Venenatis Dolor. Nulla Facilisi. In Et Sollicitudin Lacus. Donec Risus Orci, Gravida Sit Amet Risus Vehicula, Aliquet Pretium Sapien.</div>
  <div class="foot"><span>Copyright © 2023 <b>Tessaly Brink</b>. All Rights Reserved.</span><span class="pg">4</span></div>
</div>

<!-- Row 3: text slide -->
<div class="slide col-l r3">
  <svg class="slash" width="20" height="26"><line x1="16" y1="2" x2="4" y2="24" stroke="#ef8147" stroke-width="2.2"/></svg>
  <div class="s-title"><b>Heading</b> Goes Here</div>
  <div class="mark">TESSALY<br>BRINK</div>
  <div class="abs sub" style="left:48px;top:92px"><b>Heading</b> Goes Here</div>
  <div class="abs p" style="left:48px;top:118px;width:470px">
    <p>Lorem ipsum dolor sit amet, consectetur adipiscing elit. Vivamus eu dui ex. Curabitur dapibus dignissim dui, in molestie metus feugiat sed. Praesent aliquet lorem ex, eu dapibus odio varius at. Duis eget tellus porta, consequat lacus vitae, venenatis dolor. Nulla facilisi. In et sollicitudin lacus. Donec risus orci, gravida sit amet risus vehicula, aliquet pretium sapien. Nullam sit amet magna non ex bibendum mollis. Nunc vel neque eu augue dignissim congue ut vitae magna. Phasellus eget commodo arcu. Nunc vitae semper dui.</p>
    <p style="margin-top:6px">Integer venenatis, tellus sit amet interdum pretium, erat neque rhoncus turpis, a aliquam augue ligula eget erat. Nunc placerat, arcu nec mattis fermentum, nisi mauris convallis nunc, ut luctus nunc nisl id ex. Nam semper tristique mauris, et vestibulum leo fringilla vel. Nulla id augue eleifend, egestas ligula et, consequat massa. Pellentesque habitant morbi tristique senectus et netus et malesuada fames ac turpis egestas.</p>
    <p style="margin-top:6px">Lorem ipsum dolor sit amet, consectetur adipiscing elit. Vivamus eu dui ex. Curabitur dapibus dignissim dui, in molestie metus feugiat sed. Praesent aliquet lorem ex, eu dapibus odio varius at. Duis eget tellus porta, consequat lacus vitae, venenatis dolor. Nulla facilisi. In et sollicitudin lacus.</p>
  </div>
  <div class="foot"><span>Copyright © 2023 <b>Tessaly Brink</b>. All Rights Reserved.</span><span class="pg">5</span></div>
</div>

<!-- Row 3: column slide -->
<div class="slide col-r r3">
  <svg class="slash" width="20" height="26"><line x1="16" y1="2" x2="4" y2="24" stroke="#ef8147" stroke-width="2.2"/></svg>
  <div class="s-title"><b>Column</b> Slide</div>
  <div class="mark">TESSALY<br>BRINK</div>
  <div class="abs sub" style="left:48px;top:92px"><b>Heading</b> Goes Here</div>
  <div class="abs sub" style="left:291px;top:92px"><b>Heading</b> Goes Here</div>
  <div class="abs p" style="left:48px;top:118px;width:225px">Lorem ipsum dolor sit amet, consectetur adipiscing elit. Vivamus eu dui ex. Curabitur dapibus dignissim dui, in molestie metus feugiat sed. Praesent aliquet lorem ex, eu dapibus odio varius at. Duis eget tellus porta, consequat lacus vitae, venenatis dolor. Nulla facilisi. In et sollicitudin lacus. Donec risus orci, gravida sit amet risus vehicula, aliquet pretium sapien. Nullam sit amet magna non ex bibendum mollis. Nunc vel neque eu augue dignissim congue ut vitae magna. Phasellus eget commodo arcu. Nunc vitae semper dui. Integer venenatis, tellus sit amet interdum pretium, erat neque rhoncus turpis, a aliquam augue ligula eget erat. Nunc placerat, arcu nec mattis fermentum, nisi mauris convallis nunc, ut luctus nunc nisl id ex. Nam semper tristique mauris.</div>
  <div class="abs p" style="left:291px;top:118px;width:225px">Lorem ipsum dolor sit amet, consectetur adipiscing elit. Vivamus eu dui ex. Curabitur dapibus dignissim dui, in molestie metus feugiat sed. Praesent aliquet lorem ex, eu dapibus odio varius at. Duis eget tellus porta, consequat lacus vitae, venenatis dolor. Nulla facilisi. In et sollicitudin lacus. Donec risus orci, gravida sit amet risus vehicula, aliquet pretium sapien. Nullam sit amet magna non ex bibendum mollis. Nunc vel neque eu augue dignissim congue ut vitae magna. Phasellus eget commodo arcu. Nunc vitae semper dui. Integer venenatis, tellus sit amet interdum pretium, erat neque rhoncus turpis, a aliquam augue ligula eget erat. Nunc placerat, arcu nec mattis fermentum, nisi mauris convallis nunc, ut luctus nunc nisl id ex. Nam semper tristique mauris.</div>
  <div class="foot"><span>Copyright © 2023 <b>Tessaly Brink</b>. All Rights Reserved.</span><span class="pg">6</span></div>
</div>

<!-- Row 4: bullets -->
<div class="slide col-l r4">
  <svg class="slash" width="20" height="26"><line x1="16" y1="2" x2="4" y2="24" stroke="#ef8147" stroke-width="2.2"/></svg>
  <div class="s-title"><b>Bullets</b> Slide</div>
  <div class="mark">TESSALY<br>BRINK</div>
  <div class="abs sub" style="left:48px;top:92px"><b>Heading</b> Goes Here</div>
  <div class="abs sub" style="left:291px;top:92px"><b>Heading</b> Goes Here</div>
  <ul class="abs bul" style="left:48px;top:122px;width:225px">
    <li>Lorem ipsum dolor sit amet, consectetur adipiscing elit. Vivamus eu dui ex.</li>
    <li>Praesent aliquet lorem ex, eu dapibus odio varius at. Duis eget tellus porta, consequat lacus vitae, venenatis dolor. Nulla facilisi. In et sollicitudin lacus.</li>
    <li>Donec risus orci, gravida sit amet risus vehicula, aliquet pretium sapien. Nullam sit amet magna non ex bibendum mollis.</li>
    <li>Nunc vitae semper dui. Integer venenatis, tellus sit amet interdum pretium, erat neque rhoncus turpis. Curabitur dapibus dignissim dui.</li>
  </ul>
  <ul class="abs bul" style="left:291px;top:122px;width:225px">
    <li>Lorem ipsum dolor sit amet, consectetur adipiscing elit. Vivamus eu dui ex.</li>
    <li>Praesent aliquet lorem ex, eu dapibus odio varius at. Duis eget tellus porta, consequat lacus vitae, venenatis dolor. Nulla facilisi. In et sollicitudin lacus.</li>
    <li>Donec risus orci, gravida sit amet risus vehicula, aliquet pretium sapien. Nullam sit amet magna non ex bibendum mollis.</li>
    <li>Nunc vitae semper dui. Integer venenatis, tellus sit amet interdum pretium, erat neque rhoncus turpis. Curabitur dapibus dignissim dui.</li>
  </ul>
  <div class="foot"><span>Copyright © 2023 <b>Tessaly Brink</b>. All Rights Reserved.</span><span class="pg">7</span></div>
</div>

<!-- Row 4: feature with image -->
<div class="slide col-r r4">
  <svg class="abs" style="left:38px;top:40px" width="20" height="26"><line x1="16" y1="2" x2="4" y2="24" stroke="#ef8147" stroke-width="2.2"/></svg>
  <div class="abs" style="left:68px;top:40px;font-size:18px;font-weight:600;line-height:1.1;color:var(--navy)">Vivamus Eu Dui Ex.<br>Curabitur Dapibus</div>
  <div class="mark">TESSALY<br>BRINK</div>
  <div class="abs p" style="left:68px;top:97px;width:210px">Lorem Ipsum Dolor Sit Amet, Consectetur Adipiscing Elit. Vivamus Eu Dui Ex. Curabitur Dapibus Dignissim Dui, In Molestie Metus Feugiat Sed. Praesent Aliquet Lorem Ex, Eu Dapibus Odio Varius At. Nulla Facilisi. In Et Sollicitudin Lacus.</div>
  <div class="circ" style="left:64px;top:137px;width:34px;height:34px;background:var(--orange)">
    <svg width="14" height="16" viewBox="0 0 14 16"><circle cx="7" cy="6" r="5" fill="#fff"/><rect x="4.5" y="11" width="5" height="4" fill="#fff"/></svg>
  </div>
  <div class="abs" style="left:113px;top:137px;width:150px;font-size:5.2px;line-height:1.3">Lorem Ipsum Dolor Sit Amet, Consectetur Adipiscing Elit. Vivamus Eu Dui Ex. Curabitur Dapibus Dignissim Dui, In Molestie Metus Feugiat Sed. Praesent Aliquet Lorem Ex, Eu Dapibus Odio Varius At.</div>
  <div class="circ" style="left:64px;top:183px;width:34px;height:34px;background:var(--orange)">
    <svg width="16" height="16" viewBox="0 0 16 16"><circle cx="8" cy="8" r="5" fill="none" stroke="#fff" stroke-width="2.5" stroke-dasharray="3 1.6"/><circle cx="8" cy="8" r="2" fill="#fff"/></svg>
  </div>
  <div class="abs" style="left:113px;top:183px;width:150px;font-size:5.2px;line-height:1.3">Lorem Ipsum Dolor Sit Amet, Consectetur Adipiscing Elit. Vivamus Eu Dui Ex. Curabitur Dapibus Dignissim Dui, In Molestie Metus Feugiat Sed. Praesent Aliquet Lorem Ex, Eu Dapibus Odio Varius At.</div>
  <div class="abs" role="img" aria-label="Photo looking up at glass skyscrapers" style="left:300px;top:47px;width:162px;height:165px;background:linear-gradient(180deg,#c7ced6,#5a6673)"></div>
  <div class="abs" style="left:300px;top:218px;width:180px;font-size:5.2px;line-height:1.3">Lorem Ipsum Dolor Sit Amet, Consectetur Adipiscing Elit. Vivamus Eu Dui Ex. Curabitur Dapibus Dignissim Dui, In Molestie Metus Feugiat Sed. Praesent Aliquet Lorem Ex, Eu Dapibus Odio Varius At. Nulla Facilisi. In Et Sollicitudin Lacus.</div>
  <div class="foot"><span>Copyright © 2023 <b>Tessaly Brink</b>. All Rights Reserved.</span><span class="pg">8</span></div>
</div>

<!-- Row 5: icon grid -->
<div class="slide col-l r5">
  <svg class="slash" width="20" height="26"><line x1="16" y1="2" x2="4" y2="24" stroke="#ef8147" stroke-width="2.2"/></svg>
  <div class="s-title"><b>Heading</b> Goes Here</div>
  <div class="mark">TESSALY<br>BRINK</div>

  <div class="abs" style="right:343px;top:92px;width:140px;text-align:right"><div class="ttl"><b>Title</b> Goes Here!</div><div style="font-size:5px;line-height:1.3;margin-top:2px">Lorem Ipsum Dolor Sit Amet, Consectetur Adipiscing Elit. Vivamus Eu Dui Ex. Curabitur Dapibus Dignissim Dui, In Molestie Metus Feugiat Sed. Praesent Aliquet Lorem Ex.</div></div>
  <div class="abs" style="right:343px;top:151px;width:140px;text-align:right"><div class="ttl"><b>Title</b> Goes Here!</div><div style="font-size:5px;line-height:1.3;margin-top:2px">Lorem Ipsum Dolor Sit Amet, Consectetur Adipiscing Elit. Vivamus Eu Dui Ex. Curabitur Dapibus Dignissim Dui, In Molestie Metus Feugiat Sed. Praesent Aliquet Lorem Ex.</div></div>
  <div class="abs" style="right:343px;top:210px;width:140px;text-align:right"><div class="ttl"><b>Title</b> Goes Here!</div><div style="font-size:5px;line-height:1.3;margin-top:2px">Lorem Ipsum Dolor Sit Amet, Consectetur Adipiscing Elit. Vivamus Eu Dui Ex. Curabitur Dapibus Dignissim Dui, In Molestie Metus Feugiat Sed. Praesent Aliquet Lorem Ex.</div></div>

  <div class="icon-sq" style="left:234px;top:95px"><svg width="18" height="18" viewBox="0 0 18 18"><circle cx="9" cy="9" r="7" fill="none" stroke="#fff" stroke-width="1.6"/><ellipse cx="9" cy="9" rx="3" ry="7" fill="none" stroke="#fff" stroke-width="1.2"/><line x1="2" y1="9" x2="16" y2="9" stroke="#fff" stroke-width="1.2"/></svg></div>
  <div class="icon-sq" style="left:291px;top:95px"><svg width="18" height="18" viewBox="0 0 18 18"><rect x="7" y="2" width="4" height="4" fill="#fff"/><rect x="1" y="12" width="4" height="4" fill="#fff"/><rect x="7" y="12" width="4" height="4" fill="#fff"/><rect x="13" y="12" width="4" height="4" fill="#fff"/><path d="M9 6v6M3 12V9h12v3" stroke="#fff" fill="none" stroke-width="1.2"/></svg></div>
  <div class="icon-sq" style="left:234px;top:154px"><svg width="18" height="18" viewBox="0 0 18 18"><rect x="2" y="3" width="14" height="13" fill="none" stroke="#fff" stroke-width="1.6"/><line x1="2" y1="7" x2="16" y2="7" stroke="#fff" stroke-width="1.6"/><rect x="5" y="9" width="2" height="2" fill="#fff"/><rect x="8" y="9" width="2" height="2" fill="#fff"/><rect x="11" y="9" width="2" height="2" fill="#fff"/><rect x="5" y="12" width="2" height="2" fill="#fff"/><rect x="8" y="12" width="2" height="2" fill="#fff"/></svg></div>
  <div class="icon-sq" style="left:291px;top:154px"><svg width="18" height="18" viewBox="0 0 18 18"><path d="M9 9V2a7 7 0 1 1-7 7z" fill="#fff"/><path d="M10.5 1a7 7 0 0 1 6.5 6.5h-6.5z" fill="#fff"/></svg></div>
  <div class="icon-sq" style="left:234px;top:213px"><svg width="18" height="18" viewBox="0 0 18 18"><path d="M4 1h7l3 3v13H4z" fill="#fff"/><path d="M6 8h6M6 11h6M6 14h4" stroke="#ef8147" stroke-width="1"/></svg></div>
  <div class="icon-sq" style="left:291px;top:213px;color:#fff;font-weight:700;font-size:18px">$</div>

  <div class="abs" style="left:338px;top:92px;width:150px"><div class="ttl"><b>Title</b> Goes Here!</div><div style="font-size:5px;line-height:1.3;margin-top:2px">Lorem Ipsum Dolor Sit Amet, Consectetur Adipiscing Elit. Vivamus Eu Dui Ex. Curabitur Dapibus Dignissim Dui, In Molestie Metus Feugiat Sed. Praesent Aliquet Lorem Ex.</div></div>
  <div class="abs" style="left:338px;top:151px;width:150px"><div class="ttl"><b>Title</b> Goes Here!</div><div style="font-size:5px;line-height:1.3;margin-top:2px">Lorem Ipsum Dolor Sit Amet, Consectetur Adipiscing Elit. Vivamus Eu Dui Ex. Curabitur Dapibus Dignissim Dui, In Molestie Metus Feugiat Sed. Praesent Aliquet Lorem Ex.</div></div>
  <div class="abs" style="left:338px;top:210px;width:150px"><div class="ttl"><b>Title</b> Goes Here!</div><div style="font-size:5px;line-height:1.3;margin-top:2px">Lorem Ipsum Dolor Sit Amet, Consectetur Adipiscing Elit. Vivamus Eu Dui Ex. Curabitur Dapibus Dignissim Dui, In Molestie Metus Feugiat Sed. Praesent Aliquet Lorem Ex.</div></div>
  <div class="foot"><span>Copyright © 2023 <b>Tessaly Brink</b>. All Rights Reserved.</span><span class="pg">9</span></div>
</div>

<!-- Row 5: image + bullets -->
<div class="slide col-r r5">
  <svg class="full" width="563" height="315" viewBox="0 0 563 315">
    <polygon points="0,0 238,0 60,315 0,315" fill="#d9dde2" role="img" aria-label="Photo of a pen resting on a printed bar chart report"/>
    <polygon points="238,0 271,0 93,315 60,315" fill="#ef8147"/>
  </svg>
  <div class="mark">TESSALY<br>BRINK</div>
  <svg class="abs" style="left:262px;top:76px" width="20" height="26"><line x1="16" y1="2" x2="4" y2="24" stroke="#ef8147" stroke-width="2.2"/></svg>
  <div class="s-title" style="left:292px;top:78px"><b>Heading</b> Goes Here</div>
  <ul class="abs bul" style="left:292px;top:130px;width:220px">
    <li>Lorem Ipsum Dolor Sit Amet, Consectetur Adipiscing Elit.</li>
    <li>Vivamus Eu Dui Ex. Curabitur Dapibus Dignissim Dui, In Molestie Metus Feugiat Sed.</li>
    <li>Praesent Aliquet Lorem Ex, Eu Dapibus Odio Varius At. Duis Eget Tellus Porta, Consequat Lacus Vitae, Venenatis Dolor.</li>
    <li>Nulla Facilisi. In Et Sollicitudin Lacus. Donec Risus Orci, Gravida Sit Amet Risus Vehicula, Aliquet Pretium Sapien.</li>
  </ul>
  <div class="foot"><span>Copyright © 2023 <b>Tessaly Brink</b>. All Rights Reserved.</span><span class="pg">10</span></div>
</div>

<!-- Row 6: three images -->
<div class="slide col-l r6">
  <svg class="slash" width="20" height="26"><line x1="16" y1="2" x2="4" y2="24" stroke="#ef8147" stroke-width="2.2"/></svg>
  <div class="s-title"><b>Heading</b> Goes Here</div>
  <div class="mark">TESSALY<br>BRINK</div>
  <div class="abs sub" style="left:18px;top:86px;width:166px;text-align:center;font-size:8.5px"><b>Title</b> Goes Here!</div>
  <div class="abs sub" style="left:198px;top:86px;width:166px;text-align:center;font-size:8.5px"><b>Title</b> Goes Here!</div>
  <div class="abs sub" style="left:378px;top:86px;width:166px;text-align:center;font-size:8.5px"><b>Title</b> Goes Here!</div>
  <div class="abs" role="img" aria-label="Photo of a hand with a pen over charts" style="left:18px;top:104px;width:166px;height:98px;background:linear-gradient(135deg,#eef0f3,#b8c2cc)"></div>
  <div class="abs" role="img" aria-label="Photo of hands holding a tablet with a stock chart" style="left:198px;top:104px;width:166px;height:98px;background:linear-gradient(135deg,#7d8894,#2f3a46)"></div>
  <div class="abs" role="img" aria-label="Photo looking up at glass skyscrapers" style="left:378px;top:104px;width:166px;height:98px;background:linear-gradient(180deg,#c7ced6,#56626f)"></div>
  <div class="abs ph-cap" style="left:18px;top:210px;width:166px">Lorem ipsum dolor sit amet, at laborum nibh duis mauris. Per ultrices lectus sed metus tristique eu. Diam suspendisse ac ipsum maecenas.</div>
  <div class="abs ph-cap" style="left:198px;top:210px;width:166px">Lorem ipsum dolor sit amet, at laborum nibh duis mauris. Per ultrices lectus sed metus tristique eu. Diam suspendisse ac ipsum maecenas.</div>
  <div class="abs ph-cap" style="left:378px;top:210px;width:166px">Lorem ipsum dolor sit amet, at laborum nibh duis mauris. Per ultrices lectus sed metus tristique eu. Diam suspendisse ac ipsum maecenas.</div>
  <div class="foot"><span>Copyright © 2023 <b>Tessaly Brink</b>. All Rights Reserved.</span><span class="pg">11</span></div>
</div>

<!-- Row 6: orange center column -->
<div class="slide col-r r6">
  <div class="abs" style="left:189px;top:0;width:185px;height:315px;background:var(--orange)"></div>
  <div class="abs" style="left:189px;top:128px;width:185px;text-align:center;color:#fff;font-size:17px;line-height:1.15"><b style="font-weight:600">Heading</b><br>Goes Here</div>
  <div class="mark">TESSALY<br>BRINK</div>

  <div class="abs" style="left:20px;top:66px;width:135px;text-align:right"><div class="otitle">Vivamus Eu Dui Ex.<br>Curabitur Dapibus</div><div style="font-size:5px;line-height:1.3;margin-top:4px">Lorem Ipsum Dolor Sit Amet, Consectetur Adipiscing Elit. Vivamus Eu Dui Ex. Curabitur Dapibus Dignissim Dui, In Molestie Metus Feugiat Sed. Praesent Aliquet Lorem Ex, Eu Dapibus Odio Varius At. Nulla Facilisi.</div></div>
  <div class="abs" style="left:20px;top:181px;width:135px;text-align:right"><div class="otitle">Vivamus Eu Dui Ex.<br>Curabitur Dapibus</div><div style="font-size:5px;line-height:1.3;margin-top:4px">Lorem Ipsum Dolor Sit Amet, Consectetur Adipiscing Elit. Vivamus Eu Dui Ex. Curabitur Dapibus Dignissim Dui, In Molestie Metus Feugiat Sed. Praesent Aliquet Lorem Ex, Eu Dapibus Odio Varius At. Nulla Facilisi.</div></div>
  <div class="abs" style="left:408px;top:66px;width:135px"><div class="otitle">Vivamus Eu Dui Ex.<br>Curabitur Dapibus</div><div style="font-size:5px;line-height:1.3;margin-top:4px">Lorem Ipsum Dolor Sit Amet, Consectetur Adipiscing Elit. Vivamus Eu Dui Ex. Curabitur Dapibus Dignissim Dui, In Molestie Metus Feugiat Sed. Praesent Aliquet Lorem Ex, Eu Dapibus Odio Varius At. Nulla Facilisi.</div></div>
  <div class="abs" style="left:408px;top:181px;width:135px"><div class="otitle">Vivamus Eu Dui Ex.<br>Curabitur Dapibus</div><div style="font-size:5px;line-height:1.3;margin-top:4px">Lorem Ipsum Dolor Sit Amet, Consectetur Adipiscing Elit. Vivamus Eu Dui Ex. Curabitur Dapibus Dignissim Dui, In Molestie Metus Feugiat Sed. Praesent Aliquet Lorem Ex, Eu Dapibus Odio Varius At. Nulla Facilisi.</div></div>

  <div class="circ" style="left:167px;top:67px;width:44px;height:44px;background:#1e1e1e;border:3px solid #fff"><svg width="16" height="18" viewBox="0 0 16 18"><circle cx="8" cy="7" r="6" fill="#fff"/><rect x="5" y="13" width="6" height="4" fill="#fff"/></svg></div>
  <div class="circ" style="left:167px;top:182px;width:44px;height:44px;background:#1e1e1e;border:3px solid #fff"><svg width="20" height="14" viewBox="0 0 20 14"><circle cx="6" cy="4" r="3" fill="#fff"/><circle cx="14" cy="4" r="3" fill="#fff"/><path d="M0 14a6 6 0 0 1 12 0zM8 14a6 6 0 0 1 12 0z" fill="#fff"/></svg></div>
  <div class="circ" style="left:352px;top:67px;width:44px;height:44px;background:#1e1e1e;border:3px solid #fff"><svg width="18" height="18" viewBox="0 0 18 18"><circle cx="7" cy="7" r="5" fill="none" stroke="#fff" stroke-width="2.2"/><line x1="11" y1="11" x2="16" y2="16" stroke="#fff" stroke-width="2.6"/></svg></div>
  <div class="circ" style="left:352px;top:182px;width:44px;height:44px;background:#1e1e1e;border:3px solid #fff"><svg width="18" height="16" viewBox="0 0 18 16"><rect x="2" y="10" width="3" height="5" fill="#fff"/><rect x="7" y="7" width="3" height="8" fill="#fff"/><rect x="12" y="4" width="3" height="11" fill="#fff"/><path d="M1 6l6-4 4 2 6-3" stroke="#fff" fill="none" stroke-width="1.2"/></svg></div>
  <div class="foot"><span>Copyright © 2023 <b>Tessaly Brink</b>. All Rights Reserved.</span><span class="pg">12</span></div>
</div>

<!-- Row 7: chart -->
<div class="slide col-l r7">
  <svg class="slash" width="20" height="26"><line x1="16" y1="2" x2="4" y2="24" stroke="#ef8147" stroke-width="2.2"/></svg>
  <div class="s-title"><b>Heading</b> Goes Here</div>
  <div class="mark">TESSALY<br>BRINK</div>
  <svg class="abs" style="left:0;top:0" width="290" height="315" viewBox="0 0 290 315" font-family="Open Sans, sans-serif" font-size="4.5" fill="#555">
    <g stroke="#e3e3e3" stroke-width=".6">
      <line x1="52" y1="245" x2="262" y2="245"/><line x1="52" y1="223.3" x2="262" y2="223.3"/><line x1="52" y1="201.7" x2="262" y2="201.7"/><line x1="52" y1="180" x2="262" y2="180"/><line x1="52" y1="158.3" x2="262" y2="158.3"/><line x1="52" y1="136.7" x2="262" y2="136.7"/><line x1="52" y1="115" x2="262" y2="115"/>
    </g>
    <g text-anchor="end"><text x="47" y="247">0</text><text x="47" y="225">1</text><text x="47" y="203">2</text><text x="47" y="182">3</text><text x="47" y="160">4</text><text x="47" y="138">5</text><text x="47" y="117">6</text></g>
    <g fill="#ef8147"><rect x="60" y="151.8" width="7" height="93.2"/><rect x="93" y="190.8" width="7" height="54.2"/><rect x="126" y="169.2" width="7" height="75.8"/><rect x="159" y="147.5" width="7" height="97.5"/><rect x="192" y="151.8" width="7" height="93.2"/><rect x="225" y="193" width="7" height="52"/></g>
    <g fill="#9a9ea4"><rect x="68" y="193" width="7" height="52"/><rect x="101" y="149.7" width="7" height="95.3"/><rect x="134" y="206" width="7" height="39"/><rect x="167" y="169.2" width="7" height="75.8"/><rect x="200" y="190.8" width="7" height="54.2"/><rect x="233" y="149.7" width="7" height="95.3"/></g>
    <g fill="#111"><rect x="76" y="201.7" width="7" height="43.3"/><rect x="109" y="206" width="7" height="39"/><rect x="142" y="184.3" width="7" height="60.7"/><rect x="175" y="136.7" width="7" height="108.3"/><rect x="208" y="206" width="7" height="39"/><rect x="241" y="184.3" width="7" height="60.7"/></g>
    <g text-anchor="middle" font-size="4.2"><text x="71.5" y="253">Category 1</text><text x="104.5" y="253">Category 2</text><text x="137.5" y="253">Category 3</text><text x="170.5" y="253">Category 4</text><text x="203.5" y="253">Category 5</text><text x="236.5" y="253">Category 6</text></g>
  </svg>
  <div class="circ" style="left:290px;top:100px;width:30px;height:30px;background:var(--orange)"><svg width="12" height="14" viewBox="0 0 12 14"><circle cx="6" cy="4" r="3.3" fill="#fff"/><path d="M0 14a6 6 0 0 1 12 0z" fill="#fff"/></svg></div>
  <div class="circ" style="left:290px;top:156px;width:30px;height:30px;background:var(--navy)"><svg width="14" height="14" viewBox="0 0 14 14"><path d="M2 2l10 10M12 2L2 12" stroke="#fff" stroke-width="2"/></svg></div>
  <div class="circ" style="left:290px;top:212px;width:30px;height:30px;background:var(--grey)"><svg width="14" height="13" viewBox="0 0 14 13"><rect x="0" y="5" width="3" height="8" fill="#fff"/><path d="M4 5l3-5c1.5 0 2 1 1.5 3H13v3l-2 7H4z" fill="#fff"/></svg></div>
  <div class="abs" style="left:330px;top:100px;width:190px;font-size:5.3px;line-height:1.3">Lorem ipsum dolor sit amet, at laborum nibh duis mauris. Per ultrices lectus sed metus tristique eu. Diam suspendisse ac ipsum maecenas fermentum, aliquet imperdiet et lobortis venenatis nascetur lacus. A ac, vivamus erat nullam.</div>
  <div class="abs" style="left:330px;top:156px;width:190px;font-size:5.3px;line-height:1.3">Lorem ipsum dolor sit amet, at laborum nibh duis mauris. Per ultrices lectus sed metus tristique eu. Diam suspendisse ac ipsum maecenas fermentum, aliquet imperdiet et lobortis venenatis nascetur lacus. A ac, vivamus erat nullam.</div>
  <div class="abs" style="left:330px;top:212px;width:190px;font-size:5.3px;line-height:1.3">Lorem ipsum dolor sit amet, at laborum nibh duis mauris. Per ultrices lectus sed metus tristique eu. Diam suspendisse ac ipsum maecenas fermentum, aliquet imperdiet et lobortis venenatis nascetur lacus. A ac, vivamus erat nullam.</div>
  <div class="foot"><span>Copyright © 2023 <b>Tessaly Brink</b>. All Rights Reserved.</span><span class="pg">13</span></div>
</div>

<!-- Row 7: table -->
<div class="slide col-r r7">
  <svg class="slash" width="20" height="26"><line x1="16" y1="2" x2="4" y2="24" stroke="#ef8147" stroke-width="2.2"/></svg>
  <div class="s-title"><b>Heading</b> Goes Here</div>
  <div class="mark">TESSALY<br>BRINK</div>
  <table class="data">
    <tr><th style="width:160px">Heading Goes Here</th><th class="o">Heading<br>Goes Here</th><th class="g">Heading<br>Goes Here</th><th class="g">Heading<br>Goes Here</th><th class="g">Heading<br>Goes Here</th></tr>
    <tr><td>Lorem ipsum dolor sit amet</td><td>23</td><td>12</td><td>78</td><td>78</td></tr>
    <tr><td>Vivamus eu dui ex. Curabitur dapibus</td><td>45</td><td>56</td><td>12</td><td>76</td></tr>
    <tr><td>Praesent aliquet lorem ex, eu dapibus</td><td>78</td><td>76</td><td>34</td><td>34</td></tr>
    <tr><td>Duis eget tellus porta, consequat lacus</td><td>22</td><td>12</td><td>55</td><td>67</td></tr>
    <tr><td>Donec risus orci, gravida sit amet</td><td>34</td><td>66</td><td>45</td><td>11</td></tr>
    <tr><td>Nunc placerat, arcu nec mattis</td><td>67</td><td>47</td><td>78</td><td>23</td></tr>
    <tr><td>Nam semper tristique mauris</td><td>87</td><td>67</td><td>12</td><td>45</td></tr>
  </table>
  <div class="foot"><span>Copyright © 2023 <b>Tessaly Brink</b>. All Rights Reserved.</span><span class="pg">14</span></div>
</div>

<!-- Row 8: contact light -->
<div class="slide col-l r8">
  <svg class="full" width="563" height="315" viewBox="0 0 563 315">
    <polygon points="540,0 563,0 563,315 283,315" fill="#56626f" role="img" aria-label="Photo looking up at glass skyscrapers"/>
    <polygon points="515,0 540,0 283,315 257,315" fill="#ef8147"/>
  </svg>
  <div class="mark-lg" style="left:46px;top:46px;color:var(--navy)">TESSALY<br>BRINK</div>
  <div class="contact-h" style="color:var(--navy)">Contact Us</div>
  <div class="contact-row" style="top:196px;color:var(--navy)"><svg width="9" height="9" viewBox="0 0 9 9"><circle cx="4.5" cy="4.5" r="4" fill="none" stroke="#ef8147"/><path d="M3 2.5l1 2-1 1 1.5 1.5 1-1 1.5 1" stroke="#ef8147" fill="none" stroke-width=".8"/></svg>Phone Number Goes Here</div>
  <div class="contact-row" style="top:212px;color:var(--navy)"><svg width="9" height="9" viewBox="0 0 9 9"><circle cx="4.5" cy="4.5" r="4" fill="none" stroke="#ef8147"/><rect x="2.5" y="3" width="4" height="3" fill="none" stroke="#ef8147" stroke-width=".8"/></svg>E-Mail Address Goes Here</div>
  <div class="contact-row" style="top:228px;color:var(--navy)"><svg width="9" height="9" viewBox="0 0 9 9"><circle cx="4.5" cy="4.5" r="4" fill="none" stroke="#ef8147"/><line x1=".5" y1="4.5" x2="8.5" y2="4.5" stroke="#ef8147" stroke-width=".7"/><ellipse cx="4.5" cy="4.5" rx="1.8" ry="4" fill="none" stroke="#ef8147" stroke-width=".7"/></svg>URL Address Goes Here</div>
  <div class="cover-copy" style="top:268px;color:var(--navy)">Copyright © 2023 <b>Tessaly Brink</b>. All Rights Reserved.</div>
</div>

<!-- Row 8: contact dark -->
<div class="slide col-r r8" style="background:var(--navy)">
  <svg class="full" width="563" height="315" viewBox="0 0 563 315">
    <polygon points="540,0 563,0 563,315 283,315" fill="#56626f" role="img" aria-label="Photo looking up at glass skyscrapers"/>
    <polygon points="515,0 540,0 283,315 257,315" fill="#ef8147"/>
  </svg>
  <div class="mark-lg on-dark" style="left:46px;top:46px">TESSALY<br>BRINK</div>
  <div class="contact-h on-dark">Contact Us</div>
  <div class="contact-row on-dark" style="top:196px"><svg width="9" height="9" viewBox="0 0 9 9"><circle cx="4.5" cy="4.5" r="4" fill="none" stroke="#ef8147"/><path d="M3 2.5l1 2-1 1 1.5 1.5 1-1 1.5 1" stroke="#ef8147" fill="none" stroke-width=".8"/></svg>Phone Number Goes Here</div>
  <div class="contact-row on-dark" style="top:212px"><svg width="9" height="9" viewBox="0 0 9 9"><circle cx="4.5" cy="4.5" r="4" fill="none" stroke="#ef8147"/><rect x="2.5" y="3" width="4" height="3" fill="none" stroke="#ef8147" stroke-width=".8"/></svg>E-Mail Address Goes Here</div>
  <div class="contact-row on-dark" style="top:228px"><svg width="9" height="9" viewBox="0 0 9 9"><circle cx="4.5" cy="4.5" r="4" fill="none" stroke="#ef8147"/><line x1=".5" y1="4.5" x2="8.5" y2="4.5" stroke="#ef8147" stroke-width=".7"/><ellipse cx="4.5" cy="4.5" rx="1.8" ry="4" fill="none" stroke="#ef8147" stroke-width=".7"/></svg>URL Address Goes Here</div>
  <div class="cover-copy on-dark" style="top:268px">Copyright © 2023 <b>Tessaly Brink</b>. All Rights Reserved.</div>
</div>

</body>
</html>
```